Construction company business card

One side to be the logo with the company name, The other side I would like: (Tomas verbick) Project manager 41 barrow crescent hallam 52917306224783(03) 9703 2428Info@gudeljgroup.comAnd then maybe a couple dot points saying what we do:Construction (commercial & industrial) Civil construction

Anything else please contact me!
Maybe curved st one edge of the card

Target Market(s)

Older clientele

Industry/Entity Type

Construction Company

Contact Information for Business Card

Read above

Colors
3277b5
1b1b1b
9d9d9d

Requirements
Must have
• Use my logo on one side
Nice to have
• Read above
Should not have
• Read above

```html
<!DOCTYPE html>
<html lang="en">
<head>
<meta charset="utf-8">
<title>Stoutframe Property Group – Business Card</title>
<link rel="stylesheet" href="https://fonts.googleapis.com/css2?family=Roboto:wght@400;700;900&display=swap">
<style>
  :root {
    --page: #1b1b1b;
    --card: #393c40;
    --card-dark: #2f3236;
    --blue: #0a8fd6;
    --blue-deep: #3277b5;
    --grey: #9d9d9d;
    --text: #e6e7e8;
  }
  * { margin: 0; padding: 0; box-sizing: border-box; }
  html, body {
    width: 1200px; height: 1138px; overflow: hidden;
    background: var(--page);
    font-family: "Roboto", Arial, sans-serif;
    color: var(--text);
  }
  .card {
    position: absolute;
    width: 620px; height: 375px;
    background: linear-gradient(180deg, var(--card) 0%, var(--card-dark) 100%);
    border-radius: 0 30px 0 30px;
    overflow: hidden;
  }
  .card--front { left: 274px; top: 186px; }
  .card--back { left: 276px; top: 607px; }

  .front__halo {
    position: absolute; left: 340px; top: 30px;
    width: 300px; height: 300px; border-radius: 50%;
    border: 22px solid rgba(255,255,255,0.035);
  }
  .front__mark {
    position: absolute; left: 50%; top: 45px;
    width: 150px; height: 150px; margin-left: -75px;
    border-radius: 50%; background: var(--blue);
  }
  .wordmark {
    font-weight: 900; color: var(--blue);
    text-transform: uppercase; line-height: 1;
  }
  .front__wordmark {
    position: absolute; left: 0; right: 0; top: 214px;
    text-align: center;
  }
  .front__wordmark .wordmark__name { font-size: 40px; letter-spacing: 1px; display: block; }
  .front__wordmark .wordmark__sub { font-size: 15px; letter-spacing: 9px; display: block; margin-top: 6px; }
  .front__web {
    position: absolute; left: 0; right: 0; top: 300px;
    text-align: center; font-size: 15px;
    display: flex; justify-content: center; align-items: center; gap: 10px;
  }
  .front__web::before, .front__web::after {
    content: ""; width: 38px; height: 2px; background: var(--blue-deep);
  }
  .front__services {
    position: absolute; left: 0; right: 0; top: 328px;
    text-align: center; font-size: 16px;
  }
  .front__stripe {
    position: absolute; left: 0; right: 0; bottom: 0; height: 17px;
    display: flex;
  }
  .front__stripe span:first-child { flex: 1; background: var(--grey); }
  .front__stripe span:last-child { flex: 1; background: var(--blue); }

  .back__mark {
    position: absolute; left: -10px; top: 20px;
    width: 290px; height: 335px; border-radius: 50%;
    background: var(--blue);
  }
  .back__info { position: absolute; left: 317px; top: 42px; right: 20px; }
  .back__info .wordmark__name { font-size: 34px; display: block; }
  .back__info .wordmark__sub { font-size: 13px; letter-spacing: 6.5px; display: block; margin-top: 4px; }
  .contact__name {
    margin-top: 32px; font-size: 23px; font-weight: 900; color: var(--blue);
  }
  .contact__role { font-size: 16px; margin-top: 4px; }
  .contact__list { list-style: none; margin-top: 18px; font-size: 16px; }
  .contact__list li { display: flex; align-items: center; height: 23.5px; }
  .contact__list svg { width: 14px; height: 14px; margin-right: 18px; fill: var(--blue); }
  .contact__address { font-size: 16px; margin-top: 4px; }
  .contact__services { color: var(--blue); font-size: 15px; margin-top: 10px; line-height: 1.4; }
</style>
</head>
<body>

<section class="card card--front">
  <div class="front__halo"></div>
  <div class="front__mark"></div>
  <div class="wordmark front__wordmark">
    <span class="wordmark__name">Stoutframe</span>
    <span class="wordmark__sub">Property Group</span>
  </div>
  <p class="front__web">www.stoutframeproperty.com</p>
  <p class="front__services">Construction (Commercial &amp; Industrial) Civil Construction</p>
  <div class="front__stripe"><span></span><span></span></div>
</section>

<section class="card card--back">
  <div class="back__mark"></div>
  <div class="back__info">
    <div class="wordmark">
      <span class="wordmark__name">Stoutframe</span>
      <span class="wordmark__sub">Property Group</span>
    </div>
    <p class="contact__name">Tomas Verbick</p>
    <p class="contact__role">Project Manager</p>
    <ul class="contact__list">
      <li><svg viewBox="0 0 16 16"><path d="M2 10c0-5 2.5-7 6-7s6 2 6 7h-3.5V8.5h-5V10zM3 11h10l1 4H2z"/></svg>(73) 0622 4783</li>
      <li><svg viewBox="0 0 16 16"><path d="M1 3h14v10H1zM2 4.2v.8l6 4 6-4v-.8l-6 4z"/></svg>(03) 9418 6573</li>
      <li><svg viewBox="0 0 16 16"><path d="M8 1a7 7 0 1 0 0 14A7 7 0 0 0 8 1zm0 1.3c.9 0 1.9 2 2.1 5H5.9c.2-3 1.2-5 2.1-5zm0 11.4c-.9 0-1.9-2-2.1-5h4.2c-.2 3-1.2 5-2.1 5zM2.3 7.3h2.4c.1-1.8.5-3.3 1-4.3a5.7 5.7 0 0 0-3.4 4.3zm0 1.4a5.7 5.7 0 0 0 3.4 4.3c-.5-1-.9-2.5-1-4.3zm11.4 0h-2.4c-.1 1.8-.5 3.3-1 4.3a5.7 5.7 0 0 0 3.4-4.3zm0-1.4A5.7 5.7 0 0 0 10.3 3c.5 1 .9 2.5 1 4.3z"/></svg>info@verbickgroup.com</li>
    </ul>
    <p class="contact__address">41 Barrow Crescent Hallam 5291</p>
    <p class="contact__services">Construction (Commercial<br>&amp; Industrial) Civil Construction</p>
  </div>
</section>

</body>
</html>
```